Harrowgate Supply and Trade, LLC

Would like an e-commerce website started

coldbrook bearings website is a business that is almost exactly like ours...I like how in the front of the website...their lines flash across the bottom...I have attached our line card to add some of ours

we are tolk certified...I would like that to show...... attached logo

also attached our logo

```html
<!DOCTYPE html>
<html lang="en">
<head>
<meta charset="utf-8">
<title>Harrowgate Supply and Trade, LLC</title>
<link href="https://fonts.googleapis.com/css2?family=Poppins:wght@400;500;600;700;800&display=swap" rel="stylesheet">
<style>
:root{
  --green:#5b9624;
  --green-dark:#4c8019;
  --yellow:#f8c20e;
  --ink:#1e1e1e;
  --text:#444;
  --panel:#f3f3f3;
  --line:#d6d6d6;
  --white:#fff;
  --black:#000;
}
*{box-sizing:border-box;margin:0;padding:0}
html,body{width:1200px;height:4079px;overflow:hidden}
body{position:relative;font-family:'Poppins',sans-serif;color:var(--ink);background:var(--white)}
.abs{position:absolute}
a{color:inherit;text-decoration:none}

/* top bar */
.topbar{left:0;top:0;width:1200px;height:40px}
.topbar-shape{position:absolute;left:0;top:0}
.topbar-info{position:absolute;top:9px;display:flex;align-items:center;gap:6px;color:var(--white);font-size:15px;white-space:nowrap}
.topbar-info svg{width:14px;height:14px;fill:var(--white)}

/* header */
.brand{display:flex;align-items:center;gap:10px}
.brand-mark{width:26px;height:26px;background:var(--ink);flex:none}
.brand-name{font-size:17px;font-weight:600;line-height:1.15;color:var(--ink)}
.nav{left:422px;top:70px;display:flex;gap:0;font-size:15px;color:#333}
.nav a{margin-right:28px}
.cart{left:1056px;top:61px;width:36px;height:36px;border-radius:50%;background:var(--yellow);display:flex;align-items:center;justify-content:center}
.cart svg{width:16px;height:16px}

/* hero */
.hero{left:0;top:113px;width:1200px;height:470px;background:linear-gradient(180deg,#1b2a3c 0%,#3b3a36 45%,#6a4a2a 75%,#3c3129 100%)}
.hero-text{left:0;top:230px;width:1200px;text-align:center;color:var(--white)}
.hero-kicker{font-size:21px;font-weight:700;letter-spacing:.5px}
.hero-title{font-size:44px;font-weight:700;line-height:58px;margin-top:8px}
.btn{display:flex;align-items:center;justify-content:center;gap:5px;background:var(--yellow);font-weight:700;font-size:14px;color:var(--ink);clip-path:polygon(6% 0,100% 0,94% 100%,0 100%)}
.btn svg{width:12px;height:12px}
.gear-band{left:0;width:1200px;background:linear-gradient(90deg,#5b9624,#f8c20e 30%,#5b9624 55%,#f8c20e 80%,#5b9624)}

/* brands */
.section-lede{left:0;top:745px;width:1200px;text-align:center;font-size:22px;font-weight:700;line-height:36px}
.rule{height:1px;background:var(--line)}
.partners{left:96px;top:868px;display:flex;gap:6px}
.partner{width:197px;height:67px;background:#efefef;display:flex;align-items:center;justify-content:center;gap:8px;font-size:13px;font-weight:600;color:#333}
.partner.active{background:var(--white);box-shadow:0 2px 8px rgba(0,0,0,.15)}
.partner i{width:20px;height:20px;border-radius:50%;background:#333;display:block}

/* catalog */
.section-title{font-size:27px;font-weight:700}
.catalog{left:104px;top:1177px;display:grid;grid-template-columns:repeat(4,231px);column-gap:22px;row-gap:20px}
.card{position:relative;height:285px;background:var(--green);border-radius:6px;overflow:hidden}
.card-stripe{position:absolute;left:0;top:190px;width:100%;height:30px;background:var(--yellow);clip-path:polygon(0 40%,100% 0,100% 30%,0 70%)}
.card-photo{position:absolute;left:0;top:0;width:100%;height:210px;clip-path:polygon(0 0,100% 0,100% 88%,0 100%)}
.card-label{position:absolute;left:0;bottom:28px;width:100%;text-align:center;color:var(--white);font-weight:700;font-size:17px}

/* services */
.services-photo{left:109px;top:1990px;width:500px;height:440px;background:linear-gradient(135deg,#3d5870,#8a9aa8 40%,#d8c840 60%,#6a6a5a);border-radius:6px 0 0 6px}
.services-panel{left:556px;top:1990px}
.services-title{left:600px;top:2040px;font-size:26px;font-weight:700}
.service{left:600px;display:flex;gap:16px}
.service-icon{width:60px;height:60px;border-radius:50%;background:var(--yellow);display:flex;align-items:center;justify-content:center;flex:none}
.service-icon svg{width:32px;height:32px;fill:none;stroke:var(--ink);stroke-width:2}
.service h3{font-size:20px;font-weight:500;margin-top:-4px}
.service p{font-size:11.5px;color:var(--text);line-height:21px;margin-top:4px;width:330px}

/* about */
.about-copy{left:104px;top:2610px;width:430px;color:var(--white)}
.about-copy h2{font-size:27px;font-weight:700}
.about-copy p{font-size:12.5px;line-height:25.5px;margin-top:10px}

/* contact */
.map{left:104px;top:3075px;width:496px;height:393px;background:linear-gradient(135deg,#eef0f3,#dfe4ea 50%,#f1ece0)}
.contact-panel{left:530px;top:3175px;width:566px;height:375px;background:var(--panel)}
.contact-title{left:583px;top:3210px;font-size:27px;font-weight:700}
.field{position:absolute;background:#e9e9e9;border:1px solid #e0e0e0;font-size:14px;color:#555;padding:8px 12px}

/* footer */
.footer{left:0;top:3740px;width:1200px;height:339px;background:var(--black);color:var(--white)}
.footer h4{position:absolute;font-size:20px;font-weight:500;color:var(--green)}
.footer-links{position:absolute;left:419px;top:88px;font-size:15px;line-height:28px}
.contact-item{position:absolute;left:640px;width:210px;display:flex;gap:12px;align-items:center}
.contact-item .dot{width:28px;height:28px;border-radius:50%;background:var(--yellow);display:flex;align-items:center;justify-content:center;flex:none}
.contact-item .dot svg{width:15px;height:15px;fill:var(--ink)}
.contact-item b{display:block;font-size:15px;font-weight:600}
.contact-item span{font-size:12px;white-space:nowrap}
.cert{left:135px;top:183px;width:147px;height:55px;background:#3a2d7a;border:3px solid #e6e6e6}
</style>
</head>
<body>

<!-- top bar -->
<div class="abs topbar">
  <svg class="topbar-shape" width="1200" height="40"><polygon points="290,0 1200,0 1200,40 330,40" fill="#5b9624"/></svg>
  <div class="topbar-info" style="left:420px"><svg viewBox="0 0 24 24"><path d="M12 2a7 7 0 0 0-7 7c0 5 7 13 7 13s7-8 7-13a7 7 0 0 0-7-7zm0 9.5A2.5 2.5 0 1 1 12 6a2.5 2.5 0 0 1 0 5.5z"/></svg>1180 Larkspur,VA 23890</div>
  <div class="topbar-info" style="left:695px"><svg viewBox="0 0 24 24"><path d="M6.6 10.8a15 15 0 0 0 6.6 6.6l2.2-2.2a1 1 0 0 1 1-.25 11.4 11.4 0 0 0 3.6.6 1 1 0 0 1 1 1V20a1 1 0 0 1-1 1A17 17 0 0 1 3 4a1 1 0 0 1 1-1h3.5a1 1 0 0 1 1 1c0 1.25.2 2.45.6 3.6a1 1 0 0 1-.25 1z"/></svg>+555-014-2290</div>
  <div class="topbar-info" style="left:875px"><svg viewBox="0 0 24 24"><path d="M2 5h20v14H2zm2 2v.5l8 5 8-5V7z"/></svg>miles@harrowgatesupply.com</div>
</div>

<!-- header -->
<div class="abs brand" style="left:104px;top:42px">
  <span class="brand-mark"></span>
  <span class="brand-name">Harrowgate Supply<br>&amp; Trade, LLC</span>
</div>
<nav class="abs nav"><a>Home</a><a>Products</a><a>Shop Catalog</a><a>Line Card</a><a>Promotions</a><a>Company Info</a></nav>
<div class="abs cart"><svg viewBox="0 0 24 24"><path d="M6 8h12l-1 13H7z" fill="#1e1e1e"/><path d="M9 8V6a3 3 0 0 1 6 0v2" fill="none" stroke="#1e1e1e" stroke-width="2"/></svg></div>

<!-- hero -->
<div class="abs hero" role="img" aria-label="Warehouse interior with tall racks of stocked industrial parts"></div>
<div class="abs hero-text">
  <div class="hero-kicker">WELCOME TO</div>
  <div class="hero-title">HARROWGATE<br>SUPPLY AND TRADE</div>
</div>
<a class="abs btn" style="left:523px;top:410px;width:155px;height:40px">GET A QUOTE <svg viewBox="0 0 24 24"><circle cx="12" cy="12" r="11" fill="#1e1e1e"/><path d="M9 7l5 5-5 5" stroke="#f8c20e" stroke-width="3" fill="none"/></svg></a>
<div class="abs gear-band" style="top:520px;height:170px;clip-path:polygon(0 30%,100% 30%,100% 75%,0 75%)" role="img" aria-label="Row of green, yellow and white gears"></div>

<!-- brands -->
<div class="abs section-lede">SERVING INDUSTRIAL &amp; AGRICULTURAL NEEDS WITH THE BEST BRANDS<br>IN THE INDUSTRY</div>
<div class="abs rule" style="left:104px;top:827px;width:992px"></div>
<div class="abs partners">
  <div class="partner"><i></i>Norvale</div>
  <div class="partner"><i></i>Mechwright</div>
  <div class="partner active"><i></i>Ferrocrest</div>
  <div class="partner"><i></i>Ironmark</div>
  <div class="partner"><i></i>Stellan Works</div>
</div>
<div class="abs rule" style="left:0;top:1012px;width:1200px;background:#9a9a9a"></div>

<!-- catalog -->
<div class="abs section-title" style="left:0;top:1070px;width:1200px;text-align:center">CATALOG</div>
<div class="abs catalog">
  <div class="card"><div class="card-stripe"></div><div class="card-photo" role="img" aria-label="Bearing puller tool on wood" style="background:linear-gradient(135deg,#c49a62,#8a8f96)"></div><div class="card-label">Bearing Pullers</div></div>
  <div class="card"><div class="card-stripe"></div><div class="card-photo" role="img" aria-label="Steel ball bearings" style="background:linear-gradient(135deg,#5b5b5b,#c8c8c8 50%,#8a7a3a)"></div><div class="card-label">Bearing</div></div>
  <div class="card"><div class="card-stripe"></div><div class="card-photo" role="img" aria-label="Toothed drive belt" style="background:linear-gradient(135deg,#2c2c2c,#7a7a7a)"></div><div class="card-label">Belting</div></div>
  <div class="card"><div class="card-stripe"></div><div class="card-photo" role="img" aria-label="Plastic conveyor belt with bottles" style="background:linear-gradient(135deg,#1d4d7a,#5a8ab5 50%,#d59a1a)"></div><div class="card-label">Belting Plastic</div></div>
  <div class="card"><div class="card-stripe"></div><div class="card-photo" role="img" aria-label="Row of metal bin boxes" style="background:linear-gradient(135deg,#6c7a88,#d6dde4 50%,#4a5560)"></div><div class="card-label">Bin Boxes</div></div>
  <div class="card"><div class="card-stripe"></div><div class="card-photo" role="img" aria-label="Brake and clutch disc" style="background:linear-gradient(135deg,#111,#4a4a4a)"></div><div class="card-label">Brakes &amp; Clutches</div></div>
  <div class="card"><div class="card-stripe"></div><div class="card-photo" role="img" aria-label="Orange caster wheel" style="background:linear-gradient(135deg,#8a8a8a,#d6623a 55%,#3a3a3a)"></div><div class="card-label">Casters</div></div>
  <div class="card"><div class="card-stripe"></div><div class="card-photo" role="img" aria-label="Chain and sprockets" style="background:linear-gradient(135deg,#2a2a2a,#9a9a9a)"></div><div class="card-label">Chain Sprockets</div></div>
</div>
<a class="abs btn" style="left:523px;top:1820px;width:155px;height:37px">VIEW MORE <svg viewBox="0 0 24 24"><circle cx="12" cy="12" r="11" fill="#1e1e1e"/><path d="M9 7l5 5-5 5" stroke="#f8c20e" stroke-width="3" fill="none"/></svg></a>
<div class="abs rule" style="left:0;top:1912px;width:1200px;background:#9a9a9a"></div>

<!-- services -->
<div class="abs services-photo" role="img" aria-label="Two engineers in hard hats and safety vests reviewing plans"></div>
<svg class="abs services-panel" width="540" height="440"><path d="M56 0H540V440H0C40 300 20 80 56 0Z" fill="#f3f3f3"/></svg>
<div class="abs services-title">OUR SERVICES</div>
<div class="abs service" style="top:2113px">
  <div class="service-icon"><svg viewBox="0 0 32 32"><rect x="6" y="7" width="20" height="13" rx="1"/><path d="M12 25h8M16 20v5"/></svg></div>
  <div><h3>Computer-Aided Design</h3><p>Lorem ipsum dolor sit amet, consectetur adipiscing elit, sed do eiusmod tempor incididunt ut aliqua.</p></div>
</div>
<div class="abs service" style="top:2220px">
  <div class="service-icon"><svg viewBox="0 0 32 32"><path d="M7 7l18 18M25 7L7 25"/><circle cx="7" cy="7" r="3"/><circle cx="25" cy="7" r="3"/></svg></div>
  <div><h3>Fabrication and installation</h3><p>Lorem ipsum dolor sit amet, consectetur adipiscing elit, sed do eiusmod tempor incididunt ut aliqua.</p></div>
</div>
<div class="abs service" style="top:2327px">
  <div class="service-icon"><svg viewBox="0 0 32 32"><rect x="8" y="7" width="16" height="20" rx="1"/><path d="M13 5h6v4h-6zM12 14h8M12 18h8M12 22h5"/></svg></div>
  <div><h3>Plant surveys</h3><p>Lorem ipsum dolor sit amet, consectetur adipiscing elit, sed do eiusmod tempor incididunt ut aliqua.</p></div>
</div>

<!-- about -->
<svg class="abs" style="left:0;top:2578px" width="700" height="403"><path d="M0 0H650C600 80 600 320 690 403H0Z" fill="#5b9624"/></svg>
<svg class="abs" style="left:578px;top:2535px" width="622" height="460" role="img" aria-label="Company storefront building with vehicles parked out front"><defs><linearGradient id="storefront" x1="0" y1="0" x2="0" y2="1"><stop offset="0" stop-color="#5e7d3c"/><stop offset=".45" stop-color="#c9c9c4"/><stop offset=".8" stop-color="#6a6a62"/><stop offset="1" stop-color="#8a8a84"/></linearGradient></defs><path d="M140 0H622V460H150C10 380 -20 120 140 0Z" fill="url(#storefront)"/></svg>
<div class="abs about-copy">
  <h2>ABOUT US</h2>
  <p>Lorem ipsum dolor sit amet, consectetur adipiscing elit, sed do eiusmod tempor incididunt ut labore et dolore magna aliqua. Quis ipsum suspendisse ultrices gravida. Risus commodo viverra maecenas accumsan lacus vel facilisis.</p>
  <p style="margin-top:4px">Sed ut perspiciatis unde omnis iste natus error sit voluptatem accusantium doloremque laudantium, totam rem aperiam, eaque ipsa quae ab illo inventore veritatis et quasi architecto beatae vitae dicta sunt explicabo.</p>
</div>
<a class="abs btn" style="left:105px;top:2885px;width:157px;height:37px">READ MORE <svg viewBox="0 0 24 24"><circle cx="12" cy="12" r="11" fill="#1e1e1e"/><path d="M9 7l5 5-5 5" stroke="#f8c20e" stroke-width="3" fill="none"/></svg></a>

<!-- contact -->
<div class="abs map" role="img" aria-label="Street map showing the store location"></div>
<div class="abs contact-panel"></div>
<div class="abs contact-title">CONTACT US</div>
<div class="field" style="left:588px;top:3258px;width:212px;height:32px">Name</div>
<div class="field" style="left:815px;top:3258px;width:212px;height:32px">Email</div>
<div class="field" style="left:588px;top:3303px;width:212px;height:32px">Phone</div>
<div class="field" style="left:815px;top:3303px;width:212px;height:32px">Service</div>
<div class="field" style="left:588px;top:3348px;width:439px;height:72px">Message</div>
<a class="abs btn" style="left:585px;top:3475px;width:115px;height:37px">SUBMIT <svg viewBox="0 0 24 24"><circle cx="12" cy="12" r="11" fill="#1e1e1e"/><path d="M9 7l5 5-5 5" stroke="#f8c20e" stroke-width="3" fill="none"/></svg></a>

<!-- footer -->
<div class="abs gear-band" style="top:3580px;height:165px;background:linear-gradient(90deg,#111,#5b9624 20%,#f8c20e 40%,#111 55%,#5b9624 75%,#f8c20e 90%,#111)" role="img" aria-label="Row of green, yellow and white gears on black"></div>
<footer class="abs footer">
  <div class="abs brand" style="left:110px;top:62px">
    <span class="brand-mark" style="background:var(--white)"></span>
    <span class="brand-name" style="color:var(--white);font-size:21px">Harrowgate Supply<br>&amp; Trade, LLC</span>
  </div>
  <div class="abs cert" aria-label="Certification badge"></div>

  <h4 style="left:413px;top:50px">Quick Links</h4>
  <div class="footer-links"><div>Home</div><div>Products</div><div>Shop Catalog</div><div>Line Card</div><div>Promotions</div><div>Company Info</div></div>

  <h4 style="left:640px;top:50px">Contact Us</h4>
  <div class="contact-item" style="top:95px"><span class="dot"><svg viewBox="0 0 24 24"><path d="M12 2a7 7 0 0 0-7 7c0 5 7 13 7 13s7-8 7-13a7 7 0 0 0-7-7zm0 9.5A2.5 2.5 0 1 1 12 6a2.5 2.5 0 0 1 0 5.5z"/></svg></span><div><b>Location :</b><span>1180 Larkspur,VA 23890</span></div></div>
  <div class="contact-item" style="top:150px"><span class="dot"><svg viewBox="0 0 24 24"><path d="M6.6 10.8a15 15 0 0 0 6.6 6.6l2.2-2.2a1 1 0 0 1 1-.25 11.4 11.4 0 0 0 3.6.6 1 1 0 0 1 1 1V20a1 1 0 0 1-1 1A17 17 0 0 1 3 4a1 1 0 0 1 1-1h3.5a1 1 0 0 1 1 1c0 1.25.2 2.45.6 3.6a1 1 0 0 1-.25 1z"/></svg></span><div><b>Phone Number :</b><span>555 - 014 - 2290</span></div></div>
  <div class="contact-item" style="top:205px"><span class="dot"><svg viewBox="0 0 24 24"><path d="M2 5h20v14H2zm2 2v.5l8 5 8-5V7z"/></svg></span><div><b>Email :</b><span>miles@harrowgatesupply.com</span></div></div>

  <h4 style="left:871px;top:44px">Newsletter</h4>
  <div class="field" style="left:871px;top:90px;width:267px;height:32px;background:var(--white);color:#333;padding:5px 8px">Enter Email</div>
  <div class="abs btn" style="left:871px;top:135px;width:91px;height:30px;clip-path:none">SUBMIT</div>

  <div class="abs rule" style="left:104px;top:270px;width:992px;background:#777"></div>
  <div class="abs" style="left:0;top:292px;width:1200px;text-align:center;font-size:12px">©Copyrights 2024 Harrowgate Supply and Trade | All Rights Reserved</div>
</footer>

</body>
</html>
```